International business needs business cards

Our company, DRV Ventures Inc. is in the business of supplying a range construction products with particular emphasis on CEMENT. We have developed our own brand - TORVAN SUPPLIES - with which to infiltrate the market. We are launching our brand of cement (TORVAN Type IS Cement) into the Caribbean which is unlike anything this market has ever seen. A monopoly has existed here for the past 60-odd years and the market has now opened to allow the importation of other brands and consumers are anxious and ready for change/improvement. We are very excited to be launching and want to make a great first impression. We will be conducting workshops and seminars (from government level to the hardware store owners) and we want our business card to give us the strong, confident introduction that we need.

Target Market(s)

construction; builders; engineers; home owners

Industry/Entity Type

Construction

Contact Information for Business Card

Marisol Depree
CEO
cell # 1 555 4180736
Ground floor,Lindell Plaza Suite 2734
George Town,Grand Cayman
Cayman Islands,KY1-4823
EMAIL: m.depree@drvventuresinc.example
web site drvventuresinc.example

COMPANY: skype info drv.ventures.example

second card
Yvette Brannock-Depree
CFO
CELL# 1 555 607 3941
George Town,Grand Cayman
Cayman Islands,KY1-4823
EMAIL: y.brannockdepree@drvventuresinc.example
website drvventuresinc.example

Requirements
Must have
• Business cards must display BOTH logos - DRV is the company and TORVAN is the brand.

```html
<!DOCTYPE html>
<html lang="en">
<head>
<meta charset="utf-8">
<title>DRV Ventures Inc. — Business Card</title>
<link rel="stylesheet" href="https://fonts.googleapis.com/css2?family=Source+Sans+3:wght@400;600;700&display=swap">
<style>
  :root {
    --stage: #000000;
    --card-light: #f3f3f3;
    --brand-red: #7e1416;
    --ink: #1c1c1c;
    --white: #ffffff;
    --badge-grey: #6f6f6f;
  }
  * { margin: 0; padding: 0; box-sizing: border-box; }
  html, body { width: 1200px; height: 900px; overflow: hidden; background: var(--stage); }
  body { font-family: "Source Sans 3", "Myriad Pro", sans-serif; color: var(--ink); }
  .stage { position: relative; width: 1200px; height: 900px; }

  .card { position: absolute; top: 200px; height: 502px; }
  .card--front {
    left: 265px; width: 310px;
    background: var(--card-light);
    border-radius: 58px 0 58px 0;
  }
  .card--back {
    left: 641px; width: 309px;
    background: var(--brand-red);
    border-radius: 0 58px 0 58px;
  }

  .front-brand {
    position: absolute; left: 72px; top: 55px;
    display: flex; align-items: center; gap: 12px;
  }
  .front-brand__mark { width: 78px; height: 78px; background: var(--brand-red); }
  .front-brand__name {
    font-weight: 700; color: var(--ink);
    line-height: 1; text-transform: uppercase;
  }
  .front-brand__name .big { display: block; font-size: 52px; letter-spacing: 1px; }
  .front-brand__name .small { display: block; font-size: 15px; letter-spacing: 0.3px; margin-top: 3px; }

  .person { position: absolute; left: 23px; top: 212px; }
  .person__name { font-size: 18.5px; font-weight: 600; color: var(--brand-red); line-height: 1.2; }
  .person__role { font-size: 14px; line-height: 1.3; margin-top: 1px; }

  .address { position: absolute; left: 23px; top: 267px; font-size: 14px; line-height: 21px; }

  .contacts { position: absolute; left: 23px; top: 338px; list-style: none; font-size: 14px; line-height: 21px; }
  .contacts li { display: flex; align-items: center; gap: 8px; }
  .contacts svg { width: 11px; height: 11px; fill: var(--brand-red); flex: none; }

  .brand-badge {
    position: absolute; left: 30px; top: 415px;
    width: 58px; height: 58px; border-radius: 50%;
    background: var(--badge-grey);
  }

  .back-brand {
    position: absolute; right: 68px; bottom: 36px;
    color: var(--white); font-weight: 700; text-align: center;
    text-transform: uppercase; line-height: 1;
  }
  .back-brand .big { display: block; font-size: 100px; letter-spacing: 2px; }
  .back-brand .small { display: block; font-size: 21px; letter-spacing: 0.5px; margin-top: 2px; }
</style>
</head>
<body>
<main class="stage">
  <section class="card card--front" aria-label="Card front">
    <div class="front-brand">
      <span class="front-brand__mark"></span>
      <span class="front-brand__name"><span class="big">DRV</span><span class="small">Ventures Inc.</span></span>
    </div>

    <div class="person">
      <p class="person__name">Marisol Depree</p>
      <p class="person__role">CEO</p>
    </div>

    <address class="address" style="font-style:normal">
      Ground floor, Lindell Plaza Suite 2734<br>
      George Town, Grand Cayman<br>
      Cayman Islands, KY1-4823
    </address>

    <ul class="contacts">
      <li><svg viewBox="0 0 12 12" aria-hidden="true"><path d="M2.5 0.5 L4.5 0.5 L5.3 3 L4 4.2 C4.7 5.7 6.2 7.2 7.8 8 L9 6.7 L11.5 7.5 L11.5 9.5 C11.5 10.7 10.6 11.5 9.5 11.5 C4.8 11.2 0.8 7.2 0.5 2.5 C0.5 1.4 1.3 0.5 2.5 0.5 Z"/></svg>1 555 4180736</li>
      <li><svg viewBox="0 0 12 12" aria-hidden="true"><path d="M0.5 2.5 H11.5 V9.5 H0.5 Z M1.3 3.2 L6 6.6 L10.7 3.2 V3 H1.3 Z" fill-rule="evenodd"/></svg>m.depree@drvventuresinc.example</li>
      <li><svg viewBox="0 0 12 12" aria-hidden="true"><circle cx="6" cy="6" r="5.5"/></svg>www.drvventuresinc.example</li>
    </ul>

    <div class="brand-badge" role="img" aria-label="TORVAN Supplies brand badge"></div>
  </section>

  <section class="card card--back" aria-label="Card back">
    <div class="back-brand">
      <span class="big">DRV</span>
      <span class="small">Ventures Inc.</span>
    </div>
  </section>
</main>
</body>
</html>
```